Bramble firearms training and consulting

Business card for a new firearms training company. I train persons on firearms safety, personal protection, shooting tactics and CHL.Im a Prior State trooper. I also served 4 years in IRaq as a Protection contractor with the Dept of State. Real world training for Real world situations. I would like the company name to be, BRAMBLE FIREARMS TRAINING AND CONSULTING. Im native american also. Ive provided pics. Put the name Bramble above the arrowhead but rotate the arrowhead to the right with it pointing right. Then place bramble inside the arrowhead. lets see both.
Industry/Entity Type
Business
Contact Information for Business Card
Christian Chatellier817-240-0488shadowtraining33@gmail.com

```html
<!DOCTYPE html>
<html lang="en">
<head>
<meta charset="utf-8">
<title>Bramble Firearms Training and Consulting – Business Cards</title>
<link href="https://fonts.googleapis.com/css2?family=Della+Respira&family=Raleway:wght@500&display=swap" rel="stylesheet">
<style>
  :root {
    --stage: #1e1e1e;
    --card: #f7f7f6;
    --brand-red: #7c150d;
    --ink: #111111;
    --muted: #333333;
  }
  * { box-sizing: border-box; margin: 0; padding: 0; }
  html, body { width: 1200px; height: 1000px; overflow: hidden; }
  body {
    background: var(--stage);
    position: relative;
    font-family: "Della Respira", Georgia, serif;
    color: var(--ink);
  }
  .card {
    position: absolute;
    top: 160px;
    width: 420px;
    height: 680px;
    background: var(--card);
  }
  .card--a { left: 150px; }
  .card--b { left: 630px; }

  .band {
    position: absolute;
    left: 50%;
    width: 176px;
    margin-left: -88px;
    height: 30px;
    background: var(--brand-red);
  }
  .band::after {
    content: "";
    position: absolute;
    left: 0; right: 0;
    height: 3px;
    background: var(--brand-red);
  }
  .band--top { top: 26px; }
  .band--top::after { bottom: -7px; }
  .band--bottom { bottom: 26px; }
  .band--bottom::after { top: -7px; }

  .holder {
    position: absolute;
    top: 88px;
    left: 0; right: 0;
    text-align: center;
  }
  .holder__name { font-size: 27px; font-weight: 400; letter-spacing: 0.3px; }
  .holder__role { font-size: 12px; padding-left: 60px; color: var(--muted); }

  .brand {
    position: absolute;
    top: 270px;
    left: 0; right: 0;
    text-align: center;
  }
  .card--b .brand { top: 300px; }
  .brand__name {
    display: inline-flex;
    align-items: center;
    gap: 12px;
    font-size: 50px;
    line-height: 1;
    letter-spacing: 3px;
    color: var(--brand-red);
  }
  .brand__dot {
    width: 16px; height: 16px;
    border-radius: 50%;
    background: var(--brand-red);
  }
  .brand__tagline {
    margin-top: 16px;
    font-family: "Raleway", Arial, sans-serif;
    font-weight: 500;
    font-size: 15px;
    color: var(--brand-red);
    letter-spacing: 0.3px;
  }

  .contact {
    position: absolute;
    list-style: none;
    font-size: 16px;
    line-height: 1.55;
  }
  .card--a .contact { right: 34px; bottom: 110px; }
  .card--b .contact { left: 40px; bottom: 112px; }
  .contact__item { display: flex; align-items: center; gap: 8px; white-space: nowrap; }
  .card--a .contact__item { justify-content: flex-end; }
  .contact__item--phone { padding-left: 60px; }
  .card--a .contact__item--phone { padding-left: 0; padding-right: 70px; }
  .icon { width: 17px; height: 17px; flex: none; }
</style>
</head>
<body>

  <section class="card card--a" aria-label="Business card, layout A">
    <div class="band band--top"></div>
    <header class="holder">
      <h1 class="holder__name">Dorian Pellwick</h1>
      <p class="holder__role">Trainer and Consultant</p>
    </header>
    <div class="brand">
      <div class="brand__name"><span class="brand__dot"></span>BRAMBLE</div>
      <p class="brand__tagline">FIREARMS TRAINING AND CONSULTING</p>
    </div>
    <ul class="contact">
      <li class="contact__item contact__item--phone">
        <svg class="icon" viewBox="0 0 20 20"><circle cx="10" cy="10" r="8.5" fill="none" stroke="#111" stroke-width="1.5"/><path d="M7 6l2 2-1 1.2c.6 1.3 1.5 2.2 2.8 2.8L12 11l2 2-1.3 1.3C9.5 14 6 10.5 5.7 7.3z" fill="#111"/></svg>
        555-317-9062
      </li>
      <li class="contact__item">
        <svg class="icon" viewBox="0 0 20 20"><circle cx="10" cy="10" r="8.5" fill="none" stroke="#111" stroke-width="1.5"/><rect x="5.5" y="7" width="9" height="6" fill="#111"/><path d="M5.5 7l4.5 3.5L14.5 7" fill="none" stroke="#fff" stroke-width="1"/></svg>
        bramblecourse58@mailvento.com
      </li>
      <li class="contact__item">
        <svg class="icon" viewBox="0 0 20 20"><circle cx="10" cy="10" r="8.5" fill="none" stroke="#111" stroke-width="1.5"/><path d="M10 5l5 4.5h-1.5V14h-7V9.5H5z" fill="#111"/></svg>
        48 Fenwick Lane, Harlow, VT 05714
      </li>
    </ul>
    <div class="band band--bottom"></div>
  </section>

  <section class="card card--b" aria-label="Business card, layout B">
    <div class="band band--top"></div>
    <header class="holder">
      <h1 class="holder__name">Dorian Pellwick</h1>
      <p class="holder__role">Trainer and Consultant</p>
    </header>
    <div class="brand">
      <div class="brand__name"><span class="brand__dot"></span>BRAMBLE</div>
      <p class="brand__tagline">FIREARMS TRAINING AND CONSULTING</p>
    </div>
    <ul class="contact">
      <li class="contact__item contact__item--phone">
        <svg class="icon" viewBox="0 0 20 20"><circle cx="10" cy="10" r="8.5" fill="none" stroke="#111" stroke-width="1.5"/><path d="M7 6l2 2-1 1.2c.6 1.3 1.5 2.2 2.8 2.8L12 11l2 2-1.3 1.3C9.5 14 6 10.5 5.7 7.3z" fill="#111"/></svg>
        555-317-9062
      </li>
      <li class="contact__item">
        <svg class="icon" viewBox="0 0 20 20"><circle cx="10" cy="10" r="8.5" fill="none" stroke="#111" stroke-width="1.5"/><rect x="5.5" y="7" width="9" height="6" fill="#111"/><path d="M5.5 7l4.5 3.5L14.5 7" fill="none" stroke="#fff" stroke-width="1"/></svg>
        bramblecourse58@mailvento.com
      </li>
      <li class="contact__item">
        <svg class="icon" viewBox="0 0 20 20"><circle cx="10" cy="10" r="8.5" fill="none" stroke="#111" stroke-width="1.5"/><path d="M10 5l5 4.5h-1.5V14h-7V9.5H5z" fill="#111"/></svg>
        48 Fenwick Lane, Harlow, VT 05714
      </li>
    </ul>
    <div class="band band--bottom"></div>
  </section>

</body>
</html>
```